We are a doctors medical practice
I need the business card to be eye catching and memorable,
to reflect professionalism, yet also warmth and care

the numbers need to be easy to see, for the elderly

and the logo also in a location that is large enough to see and be eye catching

Back of card:
opening hours:
Mon- Fri 8.30am to 6pm
Sat 9am to 4pm

rows for appontments, date and time
Updates

HiĀ 

Modification to company name

BROOKVALE KINDRED HEALTH MEDICAL PRACTICE

Thanks
Marla

Reason: I am look for a unique design that also fulfils the design brief

I have attempted to post a .eps and .ai file of the logo

Target Market(s)

needs to appeal to the majority, mainly adults

Industry/Entity Type

Medical

Contact Information for Business Card

company name: Brookvale Kindred Health Medical Practice
Name: Dr Marla Tobrik-Vey
Qualifications: MBBS, BMedSc, FRACGP, DRCOG, MPH, Dip Skin
Address: Shop 3/41-43 Corrow St, Wendlemere 2178
Ph: 02 9184 3025
Fax: 02 9318 6042

Requirements
Nice to have
• I like balance
gold/ silver incorporated, as well as the other colours in the logo- but not limited to these colours
a "medical" feel
Should not have
• dark or strong colours

```html
<!DOCTYPE html>
<html lang="en">
<head>
<meta charset="utf-8">
<title>Brookvale Kindred Health Medical Practice – Business Card</title>
<link href="https://fonts.googleapis.com/css2?family=Open+Sans:wght@400;600;700&display=swap" rel="stylesheet">
<style>
  :root {
    --bg: #dcdddf;
    --card-light: #f3f4f5;
    --card-mid: #e6e8ea;
    --blue: #1b7fc4;
    --blue-band: #1684cc;
    --green: #5db337;
    --gold: #f0c21a;
    --gold-pale: #fbe99a;
    --ink: #2a2a2a;
    --dots: #333;
  }
  * { box-sizing: border-box; margin: 0; padding: 0; }
  html, body { width: 1200px; height: 900px; overflow: hidden; }
  body {
    background: var(--bg);
    font-family: "Open Sans", Arial, sans-serif;
    display: flex;
    align-items: center;
    justify-content: center;
    gap: 40px;
  }
  .card {
    position: relative;
    width: 540px;
    height: 309px;
    overflow: hidden;
    box-shadow: 0 6px 18px rgba(0,0,0,.18);
  }

  /* Front */
  .card--front {
    background: linear-gradient(160deg, var(--card-light), var(--card-mid));
  }
  .front__swoosh { position: absolute; left: 0; top: 0; }
  .front__doctor {
    position: absolute; right: 28px; top: 24px; text-align: right;
  }
  .doctor__name {
    color: var(--blue); font-weight: 700; font-size: 25px; line-height: 1.15;
  }
  .doctor__quals {
    color: var(--ink); font-size: 12px; font-weight: 600; line-height: 1.35; margin-top: 4px;
  }
  .front__brand {
    position: absolute; left: 22px; top: 160px;
    display: flex; align-items: center; gap: 9px;
    white-space: nowrap;
  }
  .brand__mark {
    flex: none;
    width: 38px; height: 38px; border-radius: 50%;
    border: 3px solid var(--blue); background: #fff;
  }
  .brand__name {
    color: var(--blue); font-weight: 700; font-size: 16px;
  }
  .front__contact {
    position: absolute; left: 26px; top: 222px;
    color: var(--green); font-weight: 600; font-size: 15.5px; line-height: 1.4;
    white-space: nowrap;
  }

  /* Back */
  .card--back { background: linear-gradient(160deg, #f7f7f8, #e9eaeb); }
  .back__hours {
    height: 76px; background: var(--blue-band); color: #fff;
    display: flex; align-items: center; justify-content: center; gap: 14px;
    font-size: 20px; font-weight: 600; line-height: 1.25;
    white-space: nowrap;
  }
  .back__appointments { position: relative; padding: 10px 24px 0; }
  .appt__head {
    display: flex; justify-content: space-between; align-items: flex-end;
    font-size: 12.5px; font-weight: 700; color: var(--ink);
  }
  .appt__rows { list-style: none; margin-top: 2px; }
  .appt__row {
    height: 23px; border-bottom: 2px dotted var(--dots);
  }
</style>
</head>
<body>

  <section class="card card--front" aria-label="Business card front">
    <svg class="front__swoosh" width="540" height="309" viewBox="0 0 540 309" aria-hidden="true">
      <defs>
        <linearGradient id="goldFade" x1="0" y1="0" x2="1" y2="1">
          <stop offset="0" stop-color="#f0c21a"/>
          <stop offset="1" stop-color="#fbe99a" stop-opacity=".2"/>
        </linearGradient>
      </defs>
      <path d="M0 0 H210 C150 20 100 70 85 150 C80 190 90 240 110 309 H0 Z" fill="url(#goldFade)"/>
      <path d="M235 0 C160 25 112 80 102 160" fill="none" stroke="#f0c21a" stroke-width="5"/>
      <path d="M260 0 C185 30 135 90 128 170" fill="none" stroke="#f5d65a" stroke-width="3"/>
    </svg>

    <div class="front__doctor">
      <p class="doctor__name">Dr Marla Tobrik-Vey</p>
      <p class="doctor__quals">MBBS, BMedSc, FRACGP,<br>DRCOG, MPH, Dip Skin</p>
    </div>

    <div class="front__brand">
      <span class="brand__mark" aria-hidden="true"></span>
      <span class="brand__name">BROOKVALE KINDRED HEALTH MEDICAL PRACTICE</span>
    </div>

    <div class="front__contact">
      <p>Tel : 02 9184 3025</p>
      <p>Fax : 02 9318 6042</p>
      <p>Address : Shop 3/41-43 Corrow St, Wendlemere 2178</p>
    </div>
  </section>

  <section class="card card--back" aria-label="Business card back">
    <header class="back__hours">
      <span class="hours__label">OPENING HOURS:</span>
      <span class="hours__times">Mon- Fri 8.30am to 6pm<br>Sat 9am to 4pm</span>
    </header>
    <div class="back__appointments">
      <div class="appt__head">
        <span class="appt__label">Appontments</span>
        <span class="appt__datetime">Date &amp; Time</span>
      </div>
      <ul class="appt__rows">
        <li class="appt__row"></li>
        <li class="appt__row"></li>
        <li class="appt__row"></li>
        <li class="appt__row"></li>
        <li class="appt__row"></li>
        <li class="appt__row"></li>
        <li class="appt__row"></li>
        <li class="appt__row"></li>
      </ul>
    </div>
  </section>

</body>
</html>
```